Easy Marinade Labels for Butchery Store

Need a set of labels designed for a Butchery Shop. They will sit in the top left corner of the packets as a triangle (7cm each side). Easy because the only major requirement is the label name and some small text saying "Please ask in store to see spec sheet for ingredients". Extra points for finding a fun way to incorporate the logo and/or images of food (garlic bulbs, chilli, spices ect) to enhance the label. List of Marinade Names below: GarlicPepper Mint & RosemarySatayBBQChilli Plum & GingerSundried Tomato & BasilBuffaloHoney SoyHoi-SinPer PeriSpicy CajunTeriyakiBlack Bean Ive also attached the logo and an example of how the label might sit on a packet of meat. Thanks

Target Market(s)

Butchery Deli Shop Customers

Industry/Entity Type

Food Store

Font styles to use
Serif
Sans Serif
Decorative
Other font styles liked:
• Fun font that isn't a generic Quellbrix Font?

Colors

Designer to choose colors to be used in the design.

Requirements
Must have
• Product Name
• Small text saying "Please ask in store to see spec sheet for ingredients"
Nice to have
• Photos of ingredients that would match that type of marinade - Chilli, Garlic, Spices.
• Fenly Oak Logo - not essential if it doesn't look good on the label / doesn't fit.

```html
<!DOCTYPE html>
<html lang="en">
<head>
<meta charset="utf-8">
<title>Plum and Ginger Marinade Label</title>
<link rel="stylesheet" href="https://fonts.googleapis.com/css2?family=Caveat+Brush&family=Source+Sans+3:wght@800&display=swap">
<style>
  :root {
    --paper: #ffffff;
    --frame-yellow: #eef21a;
    --art-plum: #8a5a86;
    --art-ginger: #cdb394;
    --art-shade: #3a2418;
    --ink-white: #ffffff;
  }
  html, body {
    margin: 0;
    padding: 0;
    width: 1200px;
    height: 900px;
    overflow: hidden;
    background: var(--paper);
  }
  .label {
    position: relative;
    width: 1200px;
    height: 900px;
  }
  .label-art {
    position: absolute;
    inset: 0;
  }
  .marinade-name {
    position: absolute;
    left: 504px;
    top: 0;
    width: 240px;
    height: 0;
    margin: 0;
    font-family: "Caveat Brush", cursive;
    font-weight: 400;
    color: var(--ink-white);
    text-shadow: 2px 2px 0 rgba(0,0,0,0.55);
  }
  .marinade-name span {
    position: absolute;
    left: 0;
    width: 240px;
    text-align: center;
    white-space: nowrap;
    transform: scaleX(0.8);
  }
  .marinade-name .word-first {
    top: 358px;
    font-size: 76px;
    line-height: 76px;
    letter-spacing: 3px;
  }
  .marinade-name .word-join {
    top: 438px;
    font-size: 44px;
    line-height: 44px;
    letter-spacing: 1px;
  }
  .marinade-name .word-last {
    top: 484px;
    font-size: 76px;
    line-height: 76px;
  }
  .ingredients-note {
    position: absolute;
    left: 124px;
    width: 1000px;
    top: 602px;
    margin: 0;
    text-align: center;
    white-space: nowrap;
    font-family: "Source Sans 3", sans-serif;
    font-weight: 800;
    font-size: 24px;
    line-height: 24px;
    letter-spacing: 2px;
    color: var(--ink-white);
  }
</style>
</head>
<body>
<main class="label">
  <svg class="label-art" width="1200" height="900" viewBox="0 0 1200 900">
    <defs>
      <clipPath id="triangle-clip">
        <polygon points="620,178 152,642 1090,642"/>
      </clipPath>
      <linearGradient id="ingredient-tone" x1="0" y1="0" x2="1" y2="0.6">
        <stop offset="0" stop-color="var(--art-plum)"/>
        <stop offset="1" stop-color="var(--art-ginger)"/>
      </linearGradient>
      <linearGradient id="foot-shade" x1="0" y1="575" x2="0" y2="642" gradientUnits="userSpaceOnUse">
        <stop offset="0" stop-color="var(--art-shade)" stop-opacity="0"/>
        <stop offset="1" stop-color="var(--art-shade)" stop-opacity="0.85"/>
      </linearGradient>
    </defs>

    <g class="ingredient-artwork" role="img" aria-label="Watercolour illustration of ripe plums, ginger root and green leaves" clip-path="url(#triangle-clip)">
      <rect x="140" y="170" width="960" height="480" fill="url(#ingredient-tone)"/>
      <rect x="140" y="570" width="960" height="80" fill="url(#foot-shade)"/>
    </g>

    <polygon class="label-frame" points="620,175 145,646 1097,646" fill="none" stroke="var(--frame-yellow)" stroke-width="7" stroke-linejoin="miter"/>

    <g class="title-swashes" fill="none" stroke="var(--ink-white)" stroke-width="5" stroke-linecap="round">
      <path d="M592,436 C612,426 640,432 660,426"/>
      <path d="M584,482 C606,472 636,479 658,472"/>
    </g>
  </svg>

  <h1 class="marinade-name">
    <span class="word-first">PLUM</span>
    <span class="word-join">AND</span>
    <span class="word-last">GINGER</span>
  </h1>

  <p class="ingredients-note">PLEASE ASK IN STORE TO SEE SPEC SHEET FOR INGREDIENTS</p>
</main>
</body>
</html>
```